Calderine Coffee Bag for Retail Desing

.Our name and logo represent two things about the identity of our brand Turquoise Blue which is the color of the Honduras flag and the Guacamaya Bird (Ara Macao) national bird of Honduras we want that our logo and our packing reflects the peace that you can find by brewing your coffee and also the quality of our product which comes from one of the greatest coffee beans in the world.

We are looking for a design for our coffee bag there are some elements that we need to incorporate into the bag and we are providing you with a word document with guidelines to do it

Target Market(s)

Specialty coffee consumers is the United States

Industry/Entity Type

Product

Logo Text

CALDERINE COFFEE

Colors

Designer to choose colors to be used in the design.

Requirements
Must have
• Logo / Name of Brand
• Please Check Guidelines on Word Document
Nice to have
• The bag will be sent to print and all details are customizable feel free to be creative
Should not have

```html
<!DOCTYPE html>
<html lang="en">
<head>
<meta charset="UTF-8">
<title>Calderine Coffee – Medium Dark Retail Bag</title>
<link rel="stylesheet" href="https://fonts.googleapis.com/css2?family=Ubuntu:wght@400;500&family=Barlow:wght@500;600&display=swap">
<style>
  :root {
    --backdrop: #1b2330;
    --bag-side: #3b8fcc;
    --bag-side-light: #5aa8de;
    --bag-side-edge: #2d78b3;
    --panel-navy: #071a2b;
    --accent-blue: #3aa2e8;
    --bean-tone: #2f7fc0;
    --sketch-tone: #1e4f7a;
  }
  * { margin: 0; padding: 0; box-sizing: border-box; }
  html, body {
    width: 1200px;
    height: 1200px;
    overflow: hidden;
    background: var(--backdrop);
  }
  .canvas {
    position: relative;
    width: 1200px;
    height: 1200px;
  }
  .bag {
    position: absolute;
    left: 384px;
    top: 48px;
    width: 436px;
    height: 1112px;
    background: linear-gradient(90deg, var(--bag-side-edge) 0%, var(--bag-side) 6%, var(--bag-side-light) 12%, var(--bag-side) 15.6%, var(--bag-side) 84.4%, var(--bag-side-light) 88%, var(--bag-side) 94%, var(--bag-side-edge) 100%);
    border-radius: 6px 6px 14px 14px;
  }
  .bag__panel {
    position: absolute;
    left: 68px;
    top: 0;
    width: 300px;
    height: 100%;
    background: var(--panel-navy);
    border-radius: 0 0 8px 8px;
    color: var(--accent-blue);
    text-align: center;
  }
  .bean-pattern {
    position: absolute;
    left: 0;
    top: 0;
    width: 300px;
    height: 200px;
    background: linear-gradient(180deg, #0f3556 0%, #0b2740 60%, var(--panel-navy) 100%);
  }
  .brand-mark {
    position: absolute;
    left: 34px;
    top: 248px;
    width: 232px;
    height: 232px;
    border: 3px solid var(--accent-blue);
    border-radius: 50%;
    display: flex;
    align-items: center;
    justify-content: center;
  }
  .brand-mark__name {
    font-family: "Ubuntu", sans-serif;
    font-weight: 500;
    font-size: 25px;
    line-height: 1.2;
    letter-spacing: 2px;
    color: var(--accent-blue);
  }
  .roast {
    position: absolute;
    left: 0;
    width: 100%;
    top: 496px;
    font-family: "Ubuntu", sans-serif;
    font-weight: 500;
    font-size: 35px;
    letter-spacing: 0.5px;
  }
  .claims {
    position: absolute;
    left: 0;
    width: 100%;
    top: 568px;
    list-style: none;
    font-family: "Ubuntu", sans-serif;
    font-weight: 400;
    font-size: 19px;
    line-height: 29px;
    letter-spacing: 0.4px;
  }
  .plant-sketch {
    position: absolute;
    left: 0;
    top: 730px;
    width: 270px;
    height: 200px;
    border-radius: 40% 50% 45% 40%;
    background: radial-gradient(ellipse at 55% 50%, var(--sketch-tone) 0%, #12334f 55%, var(--panel-navy) 80%);
  }
  .origin {
    position: absolute;
    left: 0;
    width: 100%;
    top: 960px;
    font-family: "Barlow", sans-serif;
    font-weight: 600;
    font-size: 27px;
    line-height: 27px;
    letter-spacing: 0.5px;
  }
  .net-weight {
    position: absolute;
    left: 0;
    width: 100%;
    top: 1040px;
    font-family: "Barlow", sans-serif;
    font-weight: 500;
    font-size: 20px;
    line-height: 28px;
  }
</style>
</head>
<body>
  <main class="canvas">
    <section class="bag">
      <div class="bag__panel">
        <div class="bean-pattern" role="img" aria-label="Repeating pattern of sketched blue coffee beans"></div>

        <div class="brand-mark">
          <p class="brand-mark__name">CALDERINE<br>COFFEE</p>
        </div>

        <h1 class="roast">Medium Dark</h1>

        <ul class="claims">
          <li>Single Origin</li>
          <li>Small Batch Roasted</li>
          <li>Farm direct trade</li>
        </ul>

        <div class="plant-sketch" role="img" aria-label="Line sketch of a coffee branch with leaves and roasted beans"></div>

        <p class="origin">100% Honduras<br>Coffee</p>

        <p class="net-weight">NET WT 16OZ<br>(1LB 16OZ) 453g</p>
      </div>
    </section>
  </main>
</body>
</html>
```